Business card design for holistic health care clinic

We need a double-sided business card design for our holistic health care clinic that integrates our logo design and also its color scheme. My business is called Valmira. It is an integrative medicine clinic. You have already done the logo for me. Please ensure an elegant and upscale design that is not cluttered, but still has all the necessary information (please see below for details).

Target Market(s)

Wellness, fitness, rehabilitation for educated, well-traveled open-minded clients who are focused on natural, organic, balanced and preventive healthcare and lifestyle.

Industry/Entity Type

Medical

Contact Information for Business Card

Modern, clean.

Number of Pages Required

1 page

Font styles to use
Serif
Sans Serif

Colors

Designer to choose colors to be used in the design.

Requirements
Must have
• Logo on one side, all other information on the other side.
• Other information should include:
• Tobias Wrenfeld - DOE, CPT, LMT
• 4100 East Marrow Drive
• Austin, TX 78119
• 512 555 0148
• 818 555 0192
• info@ValmiraHealth.example
• t.wrenfeld@ValmiraHealth.example
Nice to have
• Darker background on front - but not totally black - shaded/dark gray.

```html
<!DOCTYPE html>
<html lang="en">
<head>
<meta charset="utf-8">
<title>Valmira Business Card</title>
<link href="https://fonts.googleapis.com/css2?family=Roboto:wght@400;700&family=Roboto+Condensed:ital,wght@1,700&display=swap" rel="stylesheet">
<style>
  :root {
    --stage: #e7e5e1;
    --card-dark: #2b2b2c;
    --card-light: #ffffff;
    --accent: #1ba3dc;
    --text-light: #e9e9e9;
    --text-muted: #5a5a5a;
  }
  * { margin: 0; padding: 0; box-sizing: border-box; }
  html, body { width: 1200px; height: 886px; overflow: hidden; }
  body {
    background: var(--stage);
    font-family: "Roboto", Arial, sans-serif;
    display: flex;
    align-items: center;
    justify-content: center;
    gap: 70px;
  }
  .card {
    border-radius: 22px;
    position: relative;
    overflow: hidden;
    box-shadow: 0 10px 30px rgba(0,0,0,.18);
  }
  .card-front {
    width: 380px;
    height: 608px;
    background: var(--card-dark);
    color: var(--text-light);
    text-align: center;
    padding-top: 70px;
  }
  .icon { width: 16px; height: 16px; fill: var(--accent); display: block; margin: 0 auto 6px; }
  .holder-name {
    font-family: "Roboto Condensed", Arial, sans-serif;
    font-weight: 700;
    font-style: italic;
    font-size: 32px;
    color: var(--accent);
    letter-spacing: .5px;
    line-height: 1;
  }
  .holder-credentials {
    font-family: "Roboto Condensed", Arial, sans-serif;
    font-weight: 700;
    font-style: italic;
    font-size: 14px;
    color: var(--accent);
    margin-top: 4px;
    letter-spacing: 1px;
  }
  .contact-block { margin-top: 30px; font-size: 15px; line-height: 1.35; letter-spacing: .4px; }
  .contact-group { margin-top: 26px; }
  .contact-line { margin-bottom: 4px; }
  .contact-line .icon { margin-bottom: 3px; width: 13px; height: 13px; }
  .front-band {
    position: absolute;
    left: 0; bottom: 0;
    width: 100%;
    height: 120px;
  }
  .card-back {
    width: 608px;
    height: 380px;
    background: var(--card-light);
    display: flex;
    flex-direction: column;
    align-items: center;
    justify-content: center;
  }
  .brand {
    display: flex;
    align-items: center;
    gap: 16px;
  }
  .brand-dot { width: 22px; height: 22px; border-radius: 50%; background: var(--accent); }
  .brand-name {
    font-family: "Roboto", Arial, sans-serif;
    font-weight: 700;
    font-size: 76px;
    color: var(--accent);
    letter-spacing: 3px;
    text-transform: uppercase;
    line-height: 1;
  }
  .brand-tagline {
    margin-top: 10px;
    font-size: 20px;
    font-weight: 700;
    color: var(--accent);
    letter-spacing: .5px;
  }
  .brand-motto {
    margin-top: 40px;
    font-size: 13px;
    color: var(--text-muted);
    letter-spacing: .5px;
  }
</style>
</head>
<body>
  <section class="card card-front">
    <svg class="icon" viewBox="0 0 16 16" aria-hidden="true"><circle cx="8" cy="5" r="3.5"/><path d="M1 16c0-4 3-6.5 7-6.5s7 2.5 7 6.5z"/></svg>
    <h1 class="holder-name">TOBIAS WRENFELD</h1>
    <p class="holder-credentials">DOS, CPT, LMT</p>

    <div class="contact-block">
      <div class="contact-group">
        <svg class="icon" viewBox="0 0 16 16" aria-hidden="true"><path d="M8 0a5.5 5.5 0 0 0-5.5 5.5C2.5 10 8 16 8 16s5.5-6 5.5-10.5A5.5 5.5 0 0 0 8 0zm0 8a2.5 2.5 0 1 1 0-5 2.5 2.5 0 0 1 0 5z"/></svg>
        <p>4100 East Marrow Drive</p>
        <p>Austin, TX 78119</p>
      </div>
      <div class="contact-group">
        <div class="contact-line">
          <svg class="icon" viewBox="0 0 16 16" aria-hidden="true"><path d="M3.6 1l2.4 3-1.5 1.8c.9 2 2.6 3.8 4.7 4.7L11 9l3 2.4-1.2 3.2C6.6 14.3 1.7 9.4 1.4 3.2z"/></svg>
          <p>512 555 0148</p>
        </div>
        <div class="contact-line">
          <svg class="icon" viewBox="0 0 16 16" aria-hidden="true"><path d="M4 0h8a1 1 0 0 1 1 1v14a1 1 0 0 1-1 1H4a1 1 0 0 1-1-1V1a1 1 0 0 1 1-1zm1 2v10h6V2zm3 11a1 1 0 1 0 0 2 1 1 0 0 0 0-2z"/></svg>
          <p>818 555 0192</p>
        </div>
        <div class="contact-line">
          <svg class="icon" viewBox="0 0 16 16" aria-hidden="true"><path d="M0 3h16v10H0zm1.5 1.2v.3L8 9l6.5-4.5v-.3z"/></svg>
          <p>t.wrenfeld@ValmiraHealth.example</p>
        </div>
        <div class="contact-line">
          <svg class="icon" viewBox="0 0 16 16" aria-hidden="true"><path d="M8 0a8 8 0 1 0 0 16A8 8 0 0 0 8 0zm5.9 7h-2.6a12 12 0 0 0-1-4.8A6 6 0 0 1 13.9 7zM8 2c.8 1 1.3 2.9 1.4 5H6.6C6.7 4.9 7.2 3 8 2zM5.7 2.2a12 12 0 0 0-1 4.8H2.1a6 6 0 0 1 3.6-4.8zM2.1 9h2.6a12 12 0 0 0 1 4.8A6 6 0 0 1 2.1 9zM8 14c-.8-1-1.3-2.9-1.4-5h2.8c-.1 2.1-.6 4-1.4 5zm2.3-.2a12 12 0 0 0 1-4.8h2.6a6 6 0 0 1-3.6 4.8z"/></svg>
          <p>www.ValmiraHealth.example</p>
        </div>
      </div>
    </div>

    <svg class="front-band" viewBox="0 0 380 120" preserveAspectRatio="none" role="img" aria-label="Blue brand decoration along the lower edge">
      <path d="M0 20 C120 60 260 80 380 120 L0 120 Z" fill="var(--accent)"/>
    </svg>
  </section>

  <section class="card card-back">
    <div class="brand">
      <span class="brand-name">Valmira</span>
      <span class="brand-dot" aria-hidden="true"></span>
    </div>
    <p class="brand-tagline">Integrative Holistic Medicine</p>
    <p class="brand-motto">It's all about your objectives</p>
  </section>
</body>
</html>
```